Copper lark buildworks

Copper lark buildworks is a small construction company.
Who is a licenced builder, Carpenter, joiner,
working on heritage ,new build, speacial projects and sometimes furniture

Industry/Entity Type

Construction

```html
<!DOCTYPE html>
<html lang="en">
<head>
<meta charset="utf-8">
<title>Copper lark buildworks – Business Card</title>
<link rel="stylesheet" href="https://fonts.googleapis.com/css2?family=Open+Sans:wght@400;600&family=Roboto+Slab:wght@400;500&display=swap">
<style>
  :root {
    --backdrop: #e8e4de;
    --card-light: #ffffff;
    --card-dark: #353535;
    --brand-green: #2fa321;
    --ink: #2e2e2e;
    --ink-soft: #444444;
    --rule: #9a9a9a;
    --name-light: #e6e6e6;
  }
  * { margin: 0; padding: 0; box-sizing: border-box; }
  html, body { width: 1200px; height: 900px; overflow: hidden; }
  body {
    background: var(--backdrop);
    position: relative;
    font-family: "Open Sans", Arial, sans-serif;
    color: var(--ink);
  }
  .card {
    position: absolute;
    top: 275px;
    width: 480px;
    height: 295px;
    box-shadow: 3px 5px 8px rgba(0,0,0,0.35);
  }
  .card--front {
    left: 115px;
    background: var(--card-light);
    border-radius: 0 48px 0 48px;
  }
  .card--back {
    left: 622px;
    background: var(--card-dark);
    border-radius: 48px 0 48px 0;
  }
  .brand-mark {
    position: absolute;
    left: 345px;
    top: 40px;
    width: 52px;
    height: 52px;
    border-radius: 50%;
    background: var(--brand-green);
  }
  .company-name {
    position: absolute;
    right: 27px;
    top: 122px;
    font-family: "Roboto Slab", Georgia, serif;
    font-size: 18px;
    font-weight: 400;
    color: var(--ink);
    white-space: nowrap;
  }
  .person-name {
    position: absolute;
    left: 28px;
    top: 147px;
    font-family: "Roboto Slab", Georgia, serif;
    font-size: 20px;
    font-weight: 400;
    color: var(--ink);
  }
  .person-name .first { color: var(--brand-green); }
  .person-role {
    position: absolute;
    left: 28px;
    top: 173px;
    font-size: 12.5px;
    color: var(--ink-soft);
  }
  .divider {
    position: absolute;
    left: 147px;
    top: 179px;
    width: 305px;
    height: 1px;
    background: var(--rule);
  }
  .address {
    position: absolute;
    left: 26px;
    top: 230px;
    font-size: 13px;
    line-height: 17px;
    color: var(--ink);
  }
  .contact-list {
    position: absolute;
    right: 27px;
    top: 193px;
    list-style: none;
    text-align: right;
    font-size: 13px;
    line-height: 17.5px;
    color: var(--ink);
  }
  .contact-list li { display: flex; justify-content: flex-end; align-items: center; gap: 6px; }
  .contact-list svg { width: 10px; height: 10px; fill: var(--brand-green); flex: none; }
  .back-brand {
    position: absolute;
    left: 0; right: 0;
    top: 112px;
    display: flex;
    justify-content: center;
    align-items: center;
    gap: 14px;
  }
  .back-brand .mark {
    width: 60px; height: 60px;
    border-radius: 50%;
    background: var(--brand-green);
  }
  .back-brand .name {
    font-family: "Roboto Slab", Georgia, serif;
    font-size: 26px;
    font-weight: 400;
    color: var(--name-light);
    white-space: nowrap;
  }
</style>
</head>
<body>
  <section class="card card--front">
    <div class="brand-mark"></div>
    <div class="company-name">Copper lark buildworks</div>
    <div class="person-name"><span class="first">Marcus</span> Hale</div>
    <div class="person-role">Managing Director</div>
    <div class="divider"></div>
    <ul class="contact-list">
      <li>044-555 018 274
        <svg viewBox="0 0 10 10"><path d="M1 3.5C1 2 2.5 1 5 1s4 1 4 2.5L7.5 4.2 6.8 3H3.2L2.5 4.2zM2.5 5h5l1 4h-7z"/></svg></li>
      <li>044-555 018 274
        <svg viewBox="0 0 10 10"><path d="M3 0h4a1 1 0 0 1 1 1v8a1 1 0 0 1-1 1H3a1 1 0 0 1-1-1V1a1 1 0 0 1 1-1zm0 1.5v6h4v-6zm2 6.7a.6.6 0 1 0 0 1.2.6.6 0 0 0 0-1.2z"/></svg></li>
      <li>hello@copperlark.com
        <svg viewBox="0 0 10 10"><path d="M0 2h10v1L5 6 0 3zM0 4l5 3 5-3v4H0z"/></svg></li>
      <li>www.copperlark.com
        <svg viewBox="0 0 10 10"><circle cx="5" cy="5" r="5"/></svg></li>
    </ul>
    <div class="address">12345, Address Goes Here<br>Country Name, 123456.</div>
  </section>

  <section class="card card--back">
    <div class="back-brand">
      <div class="mark"></div>
      <div class="name">Copper lark buildworks</div>
    </div>
  </section>
</body>
</html>
```